business card deign

Logo needs the following on it.
1. attached logo
2. Tagline - "If it keeps a drink cold or the party going...we do it!"
3. Name- Dalton Pikes, Founder and CPO
4. Address - 412 E. Carver Avenue, Ste 2207, Tampa, FL. 33917
5. Phone - 555.318.4726

```html
<!DOCTYPE html>
<html lang="en">
<head>
<meta charset="utf-8">
<title>Kelvo Business Card</title>
<link href="https://fonts.googleapis.com/css2?family=Arimo:wght@400;700&family=Roboto+Condensed:wght@700&display=swap" rel="stylesheet">
<style>
  :root {
    --backdrop: #3d3d3d;
    --card-light: #ffffff;
    --card-dark: #050505;
    --ink: #111111;
    --ink-soft: #444444;
    --ink-muted: #8a8a8a;
    --paper: #ffffff;
  }
  * { box-sizing: border-box; margin: 0; padding: 0; }
  html, body {
    width: 1200px; height: 803px; overflow: hidden;
    background: var(--backdrop);
    font-family: "Arimo", Arial, sans-serif;
  }
  .stage {
    width: 1200px; height: 803px;
    display: flex; align-items: center; justify-content: center; gap: 48px;
  }
  .card {
    width: 525px; height: 300px; border-radius: 22px;
    position: relative; overflow: hidden;
    box-shadow: 0 14px 30px rgba(0,0,0,0.35);
  }
  .card--front { background: var(--card-light); color: var(--ink); }
  .card--back { background: var(--card-dark); color: var(--paper); }

  .mark-area {
    position: absolute; left: 0; top: 0; bottom: 0; width: 250px;
  }
  .mark-area svg { width: 100%; height: 100%; display: block; }

  .front-info {
    position: absolute; right: 34px; top: 26px;
    text-align: right;
  }
  .brand-name {
    font-family: "Arimo", Arial, sans-serif;
    font-weight: 400; letter-spacing: 0.02em;
  }
  .front-info .brand-name { font-size: 20px; color: var(--ink); margin-bottom: 24px; }
  .person-name {
    font-family: "Roboto Condensed", "Arial Narrow", sans-serif;
    font-weight: 700; font-size: 19px; text-transform: uppercase; color: var(--ink);
  }
  .person-role { font-size: 12px; color: var(--ink-muted); margin-bottom: 16px; }
  .address { font-style: normal; font-size: 13px; line-height: 1.45; color: var(--ink-soft); margin-bottom: 14px; }
  .contact-list { list-style: none; font-size: 13px; line-height: 1.5; color: var(--ink-soft); }
  .contact-list li { display: flex; align-items: center; justify-content: flex-end; gap: 7px; }
  .contact-list svg { width: 11px; height: 11px; fill: var(--ink); }

  .back-lockup {
    position: absolute; inset: 0;
    display: flex; flex-direction: column; align-items: center; justify-content: center;
  }
  .brand-row { display: flex; align-items: center; gap: 14px; }
  .brand-dot { width: 22px; height: 22px; border-radius: 50%; background: var(--paper); }
  .back-lockup .brand-name { font-size: 34px; color: var(--paper); }
  .tagline { margin-top: 40px; font-size: 14px; color: var(--paper); }
</style>
</head>
<body>
<main class="stage">
  <section class="card card--front">
    <div class="mark-area" role="img" aria-label="Large brand mark decoration area">
      <svg viewBox="0 0 250 300" preserveAspectRatio="none">
        <defs>
          <linearGradient id="markTone" x1="0" y1="0" x2="1" y2="1">
            <stop offset="0" stop-color="#ffffff"/>
            <stop offset="1" stop-color="#d9d9d9"/>
          </linearGradient>
        </defs>
        <rect width="250" height="300" fill="url(#markTone)"/>
      </svg>
    </div>
    <div class="front-info">
      <div class="brand-name">Kelvo</div>
      <div class="person-name">Dalton Pikes</div>
      <div class="person-role">Founder and CPO</div>
      <address class="address">412 E. Carver Avenue<br>Ste 2207<br>Tampa, FL. 33917</address>
      <ul class="contact-list">
        <li>555.318.4726
          <svg viewBox="0 0 24 24"><path d="M6.6 10.8a15 15 0 0 0 6.6 6.6l2.2-2.2c.3-.3.7-.4 1-.2 1.1.4 2.3.6 3.6.6.6 0 1 .4 1 1V20c0 .6-.4 1-1 1A17 17 0 0 1 3 4c0-.6.4-1 1-1h3.5c.6 0 1 .4 1 1 0 1.3.2 2.5.6 3.6.1.3 0 .7-.2 1z"/></svg>
        </li>
        <li>info@kelvo.com
          <svg viewBox="0 0 24 24"><path d="M2 5h20v14H2z M4 7v.4l8 5 8-5V7z" fill-rule="evenodd"/></svg>
        </li>
        <li>www.kelvo.com
          <svg viewBox="0 0 24 24"><circle cx="12" cy="12" r="10"/></svg>
        </li>
      </ul>
    </div>
  </section>

  <section class="card card--back">
    <div class="back-lockup">
      <div class="brand-row">
        <span class="brand-dot"></span>
        <span class="brand-name">Kelvo</span>
      </div>
      <p class="tagline">If it keeps a drink cold or the party going...we do it!</p>
    </div>
  </section>
</main>
</body>
</html>
```